UI/ UX Design for ERP Software

We need a new UX/UI interface for a ERP software for property managers. Our CMMS / ERP solution is made based on responsive design technologies and is coded in PHP.
The overall UX to be similar to Tev Ulna - easy navigation, intuitive menus.

Industry/Entity Type

Property Management

Number of Pages Required

5+ page

Requirements
Must have
• Round dock buttons
Consistent icons across the application
Enough Spacing between buttons/icons/ menu
Consistent Font
Nice to have
• We would like the UX to allow the users to use the application without /minimum training.
Should not have
• we don't want anything that is classic with respect to UX

```html
<!DOCTYPE html>
<html lang="en">
<head>
<meta charset="utf-8">
<title>Domora – Active Dashboard</title>
<link href="https://fonts.googleapis.com/css2?family=Rubik:wght@400;500;700&display=swap" rel="stylesheet">
<style>
:root{
  --blue:#0a78f5;
  --blue-deep:#0b50a6;
  --rail:#1467e0;
  --rail-line:rgba(255,255,255,.14);
  --cyan:#00c2f7;
  --ink:#1c2230;
  --muted:#4a5160;
  --page:#f2f5f8;
  --card:#fafafa;
  --grid:#dcdcdc;
  --white:#ffffff;
}
*{box-sizing:border-box;margin:0;padding:0}
html,body{width:1200px;height:818px;overflow:hidden}
body{font-family:'Rubik',sans-serif;background:var(--page);color:var(--ink);position:relative}
.topbar{position:absolute;left:0;top:0;width:1200px;height:71px;background:var(--white);box-shadow:0 1px 4px rgba(0,0,0,.05)}
.brand{position:absolute;left:22px;top:24px;display:flex;align-items:center;gap:7px;font-size:22px;font-weight:500;color:var(--blue)}
.brand-mark{width:18px;height:18px;border-radius:50%;background:var(--blue)}
.search{position:absolute;left:466px;top:22px;width:438px;height:25px;border:1px solid #d8dce2;border-radius:13px;font-size:8.5px;color:#333;padding:7px 18px}
.search svg{position:absolute;right:10px;top:6px}
.bell{position:absolute;left:923px;top:21px;width:27px;height:27px;border-radius:50%;background:#1d2430}
.bell svg{position:absolute;left:7px;top:6px}
.bell-count{position:absolute;right:-1px;top:-2px;width:8px;height:8px;border-radius:50%;background:var(--blue);color:#fff;font-size:5.5px;text-align:center;line-height:8px;border:1px solid #fff}
.avatar{position:absolute;left:969px;top:21px;width:27px;height:27px;border-radius:50%;background:linear-gradient(135deg,#9aa7b4,#4d5966)}
.user-name{position:absolute;left:1006px;top:29px;font-size:8px;color:#222}
.user-caret{position:absolute;left:1068px;top:31px}
.logout{position:absolute;left:1091px;top:24px;width:60px;height:20px;border:1px solid var(--blue);border-radius:10px;font-size:7px;font-weight:500;color:var(--blue);text-align:center;line-height:18px}

.sidebar{position:absolute;left:0;top:71px;width:179px;height:747px;background:var(--blue-deep)}
.sidebar::before{content:"";position:absolute;left:0;top:0;width:38px;height:100%;background:var(--rail)}
.nav{position:relative;list-style:none;padding-top:6px}
.nav li{height:26.6px;display:flex;align-items:center;border-bottom:1px solid var(--rail-line);color:#fff;font-size:9.4px}
.nav li:last-child{border-bottom:none}
.nav .ico{width:38px;display:flex;justify-content:center}
.nav .label{padding-left:6px}

.title{position:absolute;left:222px;top:115px;font-size:20.5px;font-weight:700;color:#2f3a4d}
.title span{color:var(--blue)}
.stat{position:absolute;top:116px;display:flex;gap:10px}
.stat-ico{width:29px;height:29px;border-radius:50%;background:var(--blue);display:flex;align-items:center;justify-content:center}
.stat-text{font-size:9.3px;font-weight:500;line-height:13px;padding-top:1px}
.stat-text b{display:block;font-weight:500}

.panel{position:absolute;left:221px;top:186px;width:937px;height:545px;background:var(--white);border:1px solid #e3e6ea}
.range-bar{position:absolute;left:0;top:0;width:100%;height:50px;background:linear-gradient(90deg,#0a6df0,var(--cyan))}
.range{position:absolute;top:10px;width:99px;height:27px;border:1px solid #fff;color:#fff;font-size:9.5px;display:flex;align-items:center;justify-content:center;gap:6px}
.period{position:absolute;left:39px;top:79px;display:flex;align-items:center;gap:10px;font-size:10px;font-weight:500}
.period-ico{width:29px;height:29px;border-radius:50%;background:var(--blue);display:flex;align-items:center;justify-content:center}
.chart{position:absolute;left:39px;top:130px;width:850px;height:331px;background:var(--card);box-shadow:0 0 3px rgba(0,0,0,.08)}
.legend{position:absolute;top:488px;left:0;width:100%;font-size:9.4px;color:var(--muted);line-height:12.5px}
.legend-item{position:absolute;display:flex;gap:6px}
.swatch{width:9px;height:9px;margin-top:2px;flex:none}
.footer{position:absolute;left:179px;width:1021px;top:770px;text-align:center;font-size:9.5px;color:#333}
</style>
</head>
<body>
<header class="topbar">
  <div class="brand"><span class="brand-mark"></span>Domora</div>
  <div class="search">Search
    <svg width="12" height="12" viewBox="0 0 12 12"><circle cx="5" cy="5" r="3.8" fill="none" stroke="#333" stroke-width="1.2"/><path d="M8 8l3 3" stroke="#333" stroke-width="1.3"/></svg>
  </div>
  <div class="bell">
    <svg width="13" height="14" viewBox="0 0 13 14"><path d="M6.5 1a4 4 0 0 1 4 4v3.5l1.5 2H1l1.5-2V5a4 4 0 0 1 4-4z" fill="#fff"/><circle cx="6.5" cy="12.3" r="1.4" fill="#fff"/></svg>
    <span class="bell-count">2</span>
  </div>
  <div class="avatar" role="img" aria-label="User profile photo"></div>
  <div class="user-name">Lena Marsh</div>
  <svg class="user-caret" width="9" height="6" viewBox="0 0 9 6"><path d="M1 1l3.5 3.5L8 1" fill="none" stroke="#333" stroke-width="1.2"/></svg>
  <div class="logout">Logout ⌄</div>
</header>

<nav class="sidebar">
  <ul class="nav">
    <li><span class="ico"><svg width="11" height="9"><path d="M1 8a4.5 4.5 0 0 1 9 0z" fill="#fff"/></svg></span><span class="label">Dashboard</span></li>
    <li><span class="ico"><svg width="10" height="10"><circle cx="5" cy="3" r="2.5" fill="#fff"/><path d="M0 10a5 4 0 0 1 10 0z" fill="#fff"/></svg></span><span class="label">Customers</span></li>
    <li><span class="ico"><svg width="11" height="10"><path d="M5.5 0L11 5H9.5v5h-3V7h-2v3h-3V5H0z" fill="#fff"/></svg></span><span class="label">Properties</span></li>
    <li><span class="ico"><svg width="12" height="10"><circle cx="4" cy="3" r="2.5" fill="#fff"/><path d="M0 10a4 4 0 0 1 8 0z M7 5l1.5 1.5L12 3" fill="#fff" stroke="#fff" stroke-width="1"/></svg></span><span class="label">Tenants</span></li>
    <li><span class="ico"><svg width="11" height="8"><rect width="11" height="8" rx="1" fill="#fff"/><path d="M0 1l5.5 4L11 1" stroke="#1467e0" fill="none"/></svg></span><span class="label">Contacts</span></li>
    <li><span class="ico"><svg width="12" height="10"><circle cx="4" cy="5" r="3.5" fill="#fff"/><circle cx="4" cy="5" r="1.3" fill="#1467e0"/><circle cx="9.5" cy="3" r="2.3" fill="#fff"/></svg></span><span class="label">Contractors</span></li>
    <li><span class="ico"><svg width="12" height="10"><circle cx="4" cy="3" r="2.3" fill="#fff"/><circle cx="9" cy="3" r="2" fill="#fff"/><path d="M0 10a4 4 0 0 1 8 0zM7 10a3 3 0 0 1 5 0z" fill="#fff"/></svg></span><span class="label">Employees</span></li>
    <li><span class="ico"><svg width="9" height="11"><path d="M0 0h6l3 3v8H0z" fill="#fff"/></svg></span><span class="label">Compliance Management</span></li>
    <li><span class="ico"><svg width="12" height="10"><rect x="1.5" width="9" height="7" fill="none" stroke="#fff" stroke-width="1.5"/><rect y="8" width="12" height="2" fill="#fff"/></svg></span><span class="label">Prevent Maintenance</span></li>
    <li><span class="ico"><svg width="12" height="10"><circle cx="4" cy="3" r="2.5" fill="#fff"/><path d="M0 10a4 4 0 0 1 8 0zM8 9l3-4" fill="#fff" stroke="#fff" stroke-width="1.4"/></svg></span><span class="label">Work Orders</span></li>
    <li><span class="ico"><svg width="10" height="10"><path d="M0 0h5l5 5-5 5-5-5z" fill="#fff"/><circle cx="2.5" cy="2.5" r="1" fill="#0b50a6"/></svg></span><span class="label">Purchase Orders</span></li>
    <li><span class="ico"><svg width="11" height="11"><circle cx="4.5" cy="4.5" r="3.5" fill="none" stroke="#fff" stroke-width="1.5"/><path d="M7 7l3.5 3.5" stroke="#fff" stroke-width="1.8"/></svg></span><span class="label">Property Inspections</span></li>
    <li><span class="ico"><svg width="11" height="11"><path d="M5.5 1l3 5h-6zM1 9l2-3 2 3zM6 9l2-3 2 3z" fill="#fff"/></svg></span><span class="label">Energy Management</span></li>
    <li><span class="ico"><svg width="11" height="10"><path d="M0 3h4V1h3v2h4v7H0z" fill="#fff"/></svg></span><span class="label">Risk Management</span></li>
    <li><span class="ico"><svg width="9" height="11"><path d="M0 0h6l3 3v8H0z" fill="#fff"/><path d="M2 6h5M2 8h5" stroke="#1467e0"/></svg></span><span class="label">Project Management</span></li>
    <li><span class="ico"><svg width="7" height="11"><text x="0" y="10" font-size="11" font-weight="700" fill="#fff" font-family="Rubik,sans-serif">$</text></svg></span><span class="label">Financial - Budgeting</span></li>
    <li><span class="ico"><svg width="12" height="10"><ellipse cx="5" cy="4" rx="5" ry="3.5" fill="#fff"/><ellipse cx="8" cy="6.5" rx="4" ry="3" fill="#fff"/></svg></span><span class="label">Tenant Requests</span></li>
    <li><span class="ico"><svg width="9" height="11"><path d="M0 0h6l3 3v8H0z" fill="#fff"/><path d="M2 6h5M2 8h5" stroke="#1467e0"/></svg></span><span class="label">Reports</span></li>
    <li><span class="ico"><svg width="11" height="9"><path d="M0 1h2M4 1h7M0 4.5h2M4 4.5h7M0 8h2M4 8h7" stroke="#fff" stroke-width="1.6"/></svg></span><span class="label">Visual Reports</span></li>
    <li><span class="ico"><svg width="9" height="11"><path d="M0 0h6l3 3v8H0z" fill="#fff"/><rect x="2" y="5" width="5" height="4" fill="#1467e0"/></svg></span><span class="label">Files</span></li>
    <li><span class="ico"><svg width="12" height="9"><rect width="12" height="9" rx="1" fill="#fff"/><path d="M2 3h8M2 6h8" stroke="#1467e0"/></svg></span><span class="label">Pages</span></li>
    <li><span class="ico"><svg width="11" height="11"><circle cx="5.5" cy="5.5" r="4.5" fill="#fff" stroke="#fff" stroke-width="2" stroke-dasharray="2 1.5"/><circle cx="5.5" cy="5.5" r="1.8" fill="#1467e0"/></svg></span><span class="label">Configurations</span></li>
    <li><span class="ico"><svg width="11" height="11"><path d="M1 10l5-5" stroke="#fff" stroke-width="2"/><circle cx="7.5" cy="3.5" r="3" fill="#fff"/><circle cx="8.5" cy="2.5" r="1.2" fill="#1467e0"/></svg></span><span class="label">Settings</span></li>
  </ul>
</nav>

<h1 class="title">Active <span>Dashboard</span></h1>

<div class="stat" style="left:473px">
  <div class="stat-ico"><svg width="14" height="12"><path d="M7 0l7 6h-2v6H9V8H5v4H2V6H0z" fill="#fff"/></svg></div>
  <div class="stat-text">PROPERTIES<b>3</b></div>
</div>
<div class="stat" style="left:589px">
  <div class="stat-ico"><svg width="16" height="11"><circle cx="8" cy="3" r="2.6" fill="#fff"/><circle cx="3" cy="4" r="2" fill="#fff"/><circle cx="13" cy="4" r="2" fill="#fff"/><path d="M3 11a5 4 0 0 1 10 0zM0 10a3 3 0 0 1 5-2zM16 10a3 3 0 0 0-5-2z" fill="#fff"/></svg></div>
  <div class="stat-text">TENANTS<b>8</b></div>
</div>
<div class="stat" style="left:696px">
  <div class="stat-ico"><svg width="10" height="13"><path d="M0 0h7l3 3v10H0z" fill="#fff"/><path d="M2 6h6M2 8h6M2 10h6" stroke="#0a78f5"/></svg></div>
  <div class="stat-text">TOTAL PROPERTIES AREA<b>422,000.00 sq.ft.</b></div>
</div>
<div class="stat" style="left:880px">
  <div class="stat-ico"><svg width="10" height="13"><path d="M0 0h7l3 3v10H0z" fill="#fff"/><path d="M2 6h6M2 8h6M2 10h6" stroke="#0a78f5"/></svg></div>
  <div class="stat-text">RENTED AREA<b>233,500.00 sq.ft.</b></div>
</div>
<div class="stat" style="left:1027px">
  <div class="stat-ico"><svg width="10" height="13"><path d="M0 0h7l3 3v10H0z" fill="#fff"/><path d="M2 6h6M2 8h6M2 10h6" stroke="#0a78f5"/></svg></div>
  <div class="stat-text">VACANCIES AREA<b>188,500.00 sq.ft.</b></div>
</div>

<section class="panel">
  <div class="range-bar">
    <div class="range" style="left:324px"><svg width="9" height="9"><circle cx="4.5" cy="4.5" r="3.7" fill="none" stroke="#fff" stroke-width="1.4"/><path d="M4.5 2.5v2h1.5" stroke="#fff"/></svg>Last 7 days</div>
    <div class="range" style="left:438px"><svg width="9" height="9"><circle cx="4.5" cy="4.5" r="3.7" fill="none" stroke="#fff" stroke-width="1.4"/><path d="M4.5 2.5v2h1.5" stroke="#fff"/></svg>Last months</div>
    <div class="range" style="left:552px"><svg width="9" height="9"><circle cx="4.5" cy="4.5" r="3.7" fill="none" stroke="#fff" stroke-width="1.4"/><path d="M4.5 2.5v2h1.5" stroke="#fff"/></svg>Last 3 days</div>
    <div class="range" style="left:666px"><svg width="9" height="9"><circle cx="4.5" cy="4.5" r="3.7" fill="none" stroke="#fff" stroke-width="1.4"/><path d="M4.5 2.5v2h1.5" stroke="#fff"/></svg>Next months</div>
    <div class="range" style="left:780px"><svg width="9" height="9"><circle cx="4.5" cy="4.5" r="3.7" fill="none" stroke="#fff" stroke-width="1.4"/><path d="M4.5 2.5v2h1.5" stroke="#fff"/></svg>Next 3 months</div>
  </div>

  <div class="period">
    <div class="period-ico"><svg width="12" height="12"><rect y="1.5" width="12" height="10.5" rx="1" fill="#fff"/><path d="M3 0v3M9 0v3" stroke="#fff" stroke-width="1.4"/><path d="M2 5.5h2M5 5.5h2M8 5.5h2M2 8h2M5 8h2M8 8h2M2 10.3h2M5 10.3h2" stroke="#0a78f5" stroke-width="1.2"/></svg></div>
    12/27/2020 - 01/03/2021
  </div>

  <div class="chart">
    <svg width="850" height="331" viewBox="0 0 850 331" font-family="Rubik,sans-serif" font-size="9.5" fill="#222">
      <g stroke="#dcdcdc" stroke-width="1">
        <line x1="69" y1="45" x2="815" y2="45"/>
        <line x1="69" y1="79" x2="815" y2="79"/>
        <line x1="69" y1="113" x2="815" y2="113"/>
        <line x1="69" y1="148" x2="815" y2="148"/>
        <line x1="69" y1="182" x2="815" y2="182"/>
        <line x1="69" y1="217" x2="815" y2="217"/>
        <line x1="69" y1="251" x2="815" y2="251"/>
        <line x1="69" y1="35" x2="69" y2="277"/>
        <line x1="210" y1="251" x2="210" y2="277"/>
        <line x1="314" y1="251" x2="314" y2="277"/>
        <line x1="411" y1="251" x2="411" y2="277"/>
        <line x1="504" y1="251" x2="504" y2="277"/>
        <line x1="596" y1="251" x2="596" y2="277"/>
        <line x1="688" y1="251" x2="688" y2="277"/>
        <line x1="791" y1="251" x2="791" y2="277"/>
      </g>
      <g text-anchor="end">
        <text x="47" y="48">1.5</text>
        <text x="47" y="82">1.25</text>
        <text x="47" y="116">1</text>
        <text x="47" y="151">0.75</text>
        <text x="47" y="185">0.5</text>
        <text x="47" y="220">0.25</text>
        <text x="47" y="254">0</text>
      </g>
      <g text-anchor="middle" font-size="10">
        <text x="111" y="296">27 Dec 2020</text>
        <text x="212" y="296">28 Dec 2020</text>
        <text x="313" y="296">29 Dec 2020</text>
        <text x="411" y="296">30 Dec 2020</text>
        <text x="505" y="296">31 Dec 2020</text>
        <text x="595" y="296">01 Jan 2021</text>
        <text x="691" y="296">02 Jan 2021</text>
        <text x="789" y="296">03 Jan 2021</text>
      </g>
      <rect x="407" y="113" width="8" height="138" fill="#0a6df0"/>
    </svg>
  </div>

  <div class="legend">
    <div class="legend-item" style="left:39px"><span class="swatch" style="background:#0a6df0"></span><span>Scheduled<br>Maintenance</span></div>
    <div class="legend-item" style="left:148px"><span class="swatch" style="background:#8ee07a"></span><span>Completed Scheduled<br>Maintenance</span></div>
    <div class="legend-item" style="left:295px"><span class="swatch" style="background:#f4a35c"></span><span>Future Scheduled<br>Maintenance</span></div>
    <div class="legend-item" style="left:419px"><span class="swatch" style="background:#3b3d44"></span><span>Scheduled Work<br>Orders</span></div>
    <div class="legend-item" style="left:533px"><span class="swatch" style="background:#8a86e6"></span><span>Completed Work<br>Orders</span></div>
    <div class="legend-item" style="left:647px"><span class="swatch" style="background:#f05a78"></span><span>Property Inspections<br>in Progress</span></div>
    <div class="legend-item" style="left:778px"><span class="swatch" style="background:#e6d54a"></span><span>Completed Property<br>Inspections</span></div>
  </div>
</section>

<footer class="footer">©2021 Domora, All Rights Reserved.</footer>
</body>
</html>
```